Business Card for a New Zealand IT Startup

I need a business card for VELTA Holdings. We are a young startup based in New Zealand working in internet marketing and web development. The design should have some element connected to New Zealand, such as wave, koru or silver fern, just don't use a kiwi bird.

```html
<!DOCTYPE html>
<html lang="en">
<head>
<meta charset="utf-8">
<title>VELTA Holdings — Business Card</title>
<link rel="stylesheet" href="https://fonts.googleapis.com/css2?family=Roboto:ital,wght@0,400;0,700;1,300&family=Open+Sans:ital@1&display=swap">
<style>
  :root {
    --page: #ffffff;
    --label: #1f6fb3;
    --brand-blue: #1a6fb4;
    --card-back: #1b70b5;
    --frond-blue: #2f6497;
    --frond-shadow: #245886;
    --card-front-light: #e4e4e6;
    --card-front-mid: #cfcfd2;
    --fern-dark: #b9b8b6;
    --fern-pale: #f1f1f2;
    --fern-amber: #d9cdb9;
    --ink-white: #ffffff;
  }
  * { margin: 0; padding: 0; box-sizing: border-box; }
  html, body {
    width: 1200px; height: 1200px; overflow: hidden;
    background: var(--page);
    font-family: "Roboto", Arial, sans-serif;
  }
  .sheet { position: relative; width: 1200px; height: 1200px; }
  .side-label {
    position: absolute; left: 0; width: 1200px; text-align: center;
    font-family: "Open Sans", Arial, sans-serif; font-style: italic;
    font-size: 19px; color: var(--label);
  }
  .side-label--front { top: 136px; }
  .side-label--back { top: 1044px; }

  .card { position: absolute; left: 248px; width: 704px; overflow: hidden; }
  .card--front { top: 170px; height: 422px; background: var(--card-front-light); }
  .card--back { top: 605px; height: 424px; background: var(--card-back); }

  /* silver fern photograph area */
  .fern-photo {
    position: absolute; inset: 0;
    background:
      radial-gradient(ellipse 30% 14% at 32% 22%, var(--fern-pale) 0%, rgba(241,241,242,0) 100%),
      radial-gradient(ellipse 26% 10% at 52% 10%, var(--fern-pale) 0%, rgba(241,241,242,0) 100%),
      radial-gradient(ellipse 18% 16% at 88% 10%, var(--fern-amber) 0%, rgba(217,205,185,0) 100%),
      radial-gradient(ellipse 22% 18% at 8% 6%, var(--fern-dark) 0%, rgba(185,184,182,0) 100%),
      radial-gradient(ellipse 30% 22% at 22% 75%, var(--card-front-mid) 0%, rgba(207,207,210,0) 100%),
      linear-gradient(160deg, var(--card-front-mid) 0%, var(--card-front-light) 40%, var(--card-front-light) 100%);
  }
  .brand-name {
    position: absolute; left: 0; right: 0; top: 170px;
    display: flex; align-items: center; justify-content: center; gap: 18px;
    font-family: "Roboto", Arial, sans-serif; font-weight: 700;
    font-size: 60px; line-height: 1; letter-spacing: 1px; color: var(--brand-blue);
  }
  .brand-dot {
    width: 30px; height: 30px; border-radius: 50%; background: var(--brand-blue);
  }

  /* koru frond photograph area */
  .koru-photo {
    position: absolute; left: 440px; top: 90px; width: 220px; height: 334px;
    background:
      radial-gradient(ellipse 42% 28% at 50% 26%, var(--frond-shadow) 0%, rgba(36,88,134,0.55) 55%, rgba(36,88,134,0) 100%),
      radial-gradient(ellipse 22% 14% at 30% 62%, var(--frond-blue) 0%, rgba(47,100,151,0) 100%),
      linear-gradient(200deg, rgba(47,100,151,0) 40%, rgba(47,100,151,0.7) 55%, rgba(47,100,151,0) 72%);
  }
  .holder-name {
    position: absolute; left: 92px; top: 78px;
    font-weight: 700; font-size: 60px; line-height: 1; color: var(--ink-white);
  }
  .holder-role {
    position: absolute; left: 92px; top: 139px;
    font-weight: 300; font-style: italic; font-size: 26px; color: var(--ink-white);
  }
  .contact-list {
    position: absolute; left: 92px; top: 262px; list-style: none;
    font-size: 18.5px; color: var(--ink-white);
  }
  .contact-item { display: flex; align-items: center; height: 28px; }
  .contact-item svg { width: 17px; height: 17px; margin: 0 12px 0 2px; fill: var(--ink-white); }
  .contact-item--web { margin-top: 12px; }
</style>
</head>
<body>
<div class="sheet">
  <p class="side-label side-label--front">front</p>

  <section class="card card--front">
    <div class="fern-photo" role="img" aria-label="Soft, faded photograph of New Zealand silver fern fronds"></div>
    <div class="brand-name"><span class="brand-dot"></span><span>VELTA Holdings</span></div>
  </section>

  <section class="card card--back">
    <div class="koru-photo" role="img" aria-label="Blue-toned photograph of an unfurling koru fern frond, a New Zealand symbol"></div>
    <h1 class="holder-name">Marcus Hale</h1>
    <p class="holder-role">company position</p>
    <ul class="contact-list">
      <li class="contact-item">
        <svg viewBox="0 0 24 24" aria-hidden="true"><path d="M6.6 10.8a15.2 15.2 0 0 0 6.6 6.6l2.2-2.2a1 1 0 0 1 1-.25 11.4 11.4 0 0 0 3.6.57 1 1 0 0 1 1 1V20a1 1 0 0 1-1 1A17 17 0 0 1 3 4a1 1 0 0 1 1-1h3.5a1 1 0 0 1 1 1c0 1.25.2 2.450.57 3.57a1 1 0 0 1-.25 1z"/></svg>
        0800-372915
      </li>
      <li class="contact-item">
        <svg viewBox="0 0 24 24" aria-hidden="true"><path d="M2 5h20v14H2z M3.5 6.5v.3l8.5 6 8.5-6v-.3z M3.5 8.6v8.9h17V8.6L12 14.6z" fill-rule="evenodd"/></svg>
        marcushale@veltaholdings.com
      </li>
      <li class="contact-item contact-item--web">www.yourwebsite.com</li>
    </ul>
  </section>

  <p class="side-label side-label--back">back</p>
</div>
</body>
</html>
```